Q.I.V.A. The Caldwell Grand Jury Testimony

This is the cover artwork for the audio version
of the re-creation of the Caldwell Grand Jury testimony based around the killing of Tyrell Hawkins. I need a cover for the library binders. I have the template for the binder that I can send. The title of the audio is: Q.I.V.A. I would like the words Caldwell Grand Jury Testimony added in somehow with some creative graphics. I have a website with other audio covers. I also need the words: Unabridged CD format somewhere at the bottom. Can I send the binder template later?

Target Market(s)

Audiobook

Industry/Entity Type

Audio

Font styles to use
Serif

Requirements
Nice to have
• no bullets, no blood, no dead bodies, no police, no police cars, no protest, no
• violent images, no bullets
Should not have
• nice clear sleek look

```html
<!DOCTYPE html>
<html lang="en">
<head>
<meta charset="utf-8">
<title>Q.I.V.A. — Caldwell Grand Jury Testimony</title>
<link rel="stylesheet" href="https://fonts.googleapis.com/css2?family=Tinos:ital,wght@0,400;0,700;1,700&display=swap">
<style>
  :root {
    --ink: #5a3330;
    --paper: #ffffff;
    --accent: #e8b820;
    --glow: #d09450;
    --mid: #9a5a24;
    --edge: #4a220c;
  }
  html, body {
    margin: 0;
    padding: 0;
    width: 1200px;
    height: 1200px;
    overflow: hidden;
    background: var(--edge);
  }
  .cover {
    position: relative;
    width: 1200px;
    height: 1200px;
  }
  .cover__texture {
    position: absolute;
    inset: 0;
    background:
      radial-gradient(ellipse 55% 45% at 50% 58%, var(--glow) 0%, rgba(176,112,52,0.6) 45%, rgba(0,0,0,0) 80%),
      linear-gradient(180deg, #8a4a1c 0%, var(--mid) 45%, #8a4a1a 75%, var(--edge) 100%);
  }
  .cover__art {
    position: absolute;
    inset: 0;
    width: 1200px;
    height: 1200px;
  }
  .type { font-family: "Tinos", "Times New Roman", serif; }
  .series { font-weight: 700; fill: var(--ink); }
  .title-top { font-weight: 700; fill: var(--ink); }
  .subtitle { font-weight: 400; fill: var(--ink); }
  .initial { font-weight: 700; font-style: italic; fill: var(--paper); }
  .format { font-weight: 700; fill: var(--paper); }
  .frame { fill: none; stroke: var(--paper); stroke-width: 3; }
  .rule { stroke: var(--accent); stroke-width: 3; }
</style>
</head>
<body>
<main class="cover">
  <div class="cover__texture" role="img" aria-label="Weathered brown grunge texture with a warm glow at the centre"></div>
  <svg class="cover__art" viewBox="0 0 1500 1500" xmlns="http://www.w3.org/2000/svg">
    <rect class="frame" x="60" y="60" width="1380" height="1380"/>

    <text class="type series" x="750" y="352" font-size="140" text-anchor="middle" letter-spacing="6">Q.I.V.A.</text>

    <text class="type title-top" x="320" y="710" font-size="170" textLength="915" lengthAdjust="spacingAndGlyphs">CALDWELL</text>
    <text class="type subtitle" x="550" y="790" font-size="76" textLength="678" lengthAdjust="spacing">Grand  Jury</text>
    <text class="type title-top" x="460" y="920" font-size="140" textLength="765" lengthAdjust="spacingAndGlyphs">ESTIMONY</text>
    <text class="type initial" x="290" y="965" font-size="340">T</text>

    <line class="rule" x1="597" y1="1308" x2="933" y2="1308"/>
    <text class="type format" x="400" y="1380" font-size="30" textLength="705" lengthAdjust="spacing">Unabridged   CD   format</text>
  </svg>
</main>
</body>
</html>
```